Business card design for Virtual Assistance company

I need a business card designed for my virtual assistance company. We are a small company who services primarily C-level executive clients. The card needs to be double sided with the following contact information on the back:
Melissa Thornbury
Owner/CEO
info@rkpadvisory.net
www.rkpadvisory.net
555.302.9817

The front side should just have the company name incorporated: "RKP Advisory" and "virtual assistance"

The card should be simplistic, but eye catching and should speak to high level executives. Our primary focus areas consist of executive assistance and government contracting.

Target Market(s)

CEOs and executives

Contact Information for Business Card

see project description. phone, email, website.

Colors

Designer to choose only greyscale colors for use in the design.

```html
<!DOCTYPE html>
<html lang="en">
<head>
<meta charset="utf-8">
<title>RKP Advisory – Business Card</title>
<link rel="stylesheet" href="https://fonts.googleapis.com/css2?family=Cinzel:wght@500;600&family=Poppins:wght@300;400&display=swap">
<style>
  :root {
    --backdrop: #c4c4c4;
    --card: #050505;
    --silver: #c9c9c9;
    --silver-soft: #a6a6a6;
    --white: #f4f4f4;
    --grey: #8c8c8c;
    --edge: #9a9a9a;
    --rule: #3a3a3a;
  }
  * { box-sizing: border-box; margin: 0; padding: 0; }
  html, body {
    width: 1200px; height: 800px; overflow: hidden;
    background: var(--backdrop);
  }
  .canvas {
    position: relative; width: 1200px; height: 800px;
    display: flex; align-items: center; justify-content: center; gap: 30px;
  }
  .card {
    position: relative; width: 560px; height: 320px;
    background: var(--card);
    border-bottom: 2px solid var(--edge);
    border-left: 1px solid var(--edge);
    overflow: hidden;
  }

  /* Shared wordmark */
  .brand-name {
    font-family: "Cinzel", serif; font-weight: 600;
    text-transform: uppercase; white-space: nowrap;
  }
  .brand-tagline {
    display: flex; align-items: center; gap: 10px;
    font-family: "Poppins", sans-serif; font-weight: 400;
    text-transform: uppercase; white-space: nowrap;
  }
  .brand-tagline::before,
  .brand-tagline::after {
    content: ""; display: block; width: 22px; height: 1px; background: currentColor;
  }

  /* Back side: wordmark + contact details */
  .card-back .brand {
    position: absolute; left: 0; top: 0; width: 278px; height: 100%;
    display: flex; flex-direction: column; align-items: center; justify-content: center;
  }
  .card-back .brand-name {
    font-size: 29px; letter-spacing: 2px; color: var(--white);
  }
  .card-back .brand-tagline {
    margin-top: 8px; font-size: 10px; letter-spacing: 3px; color: var(--grey);
  }
  .divider {
    position: absolute; left: 278px; top: 50px; width: 1px; height: 220px;
    background: linear-gradient(to bottom, transparent, var(--rule) 20%, var(--rule) 80%, transparent);
  }
  .contact {
    position: absolute; left: 305px; top: 70px; right: 20px;
  }
  .contact-name {
    font-family: "Cinzel", serif; font-weight: 600;
    font-size: 19px; letter-spacing: 1px; color: var(--silver);
    text-transform: uppercase; white-space: nowrap;
  }
  .contact-role {
    font-family: "Poppins", sans-serif; font-weight: 300;
    font-size: 14px; color: var(--white); margin-top: 2px;
  }
  .contact-list { list-style: none; margin-top: 34px; }
  .contact-list li {
    display: flex; align-items: center; gap: 9px;
    font-family: "Poppins", sans-serif; font-weight: 300;
    font-size: 13px; color: var(--white); line-height: 22px; white-space: nowrap;
  }
  .contact-list svg { width: 13px; height: 13px; flex: none; color: var(--silver); }

  /* Front side: centred wordmark */
  .card-front {
    display: flex; flex-direction: column; align-items: center; justify-content: center;
  }
  .card-front .brand-name {
    font-size: 46px; letter-spacing: 3px; color: var(--silver);
  }
  .card-front .brand-tagline {
    font-size: 13px; letter-spacing: 4px; color: var(--silver-soft); margin-top: 10px;
  }
</style>
</head>
<body>
  <main class="canvas">
    <section class="card card-back" aria-label="Business card back">
      <div class="brand">
        <p class="brand-name">RKP Advisory</p>
        <p class="brand-tagline">Virtual Assistance</p>
      </div>
      <div class="divider"></div>
      <div class="contact">
        <p class="contact-name">Melissa Thornbury</p>
        <p class="contact-role">Owner/CEO</p>
        <ul class="contact-list">
          <li>
            <svg viewBox="0 0 24 24" aria-hidden="true"><path fill="currentColor" d="M6.6 10.8a15.2 15.2 0 0 0 6.6 6.6l2.2-2.2a1 1 0 0 1 1-.25 11.4 11.4 0 0 0 3.6.57 1 1 0 0 1 1 1V20a1 1 0 0 1-1 1A17 17 0 0 1 3 4a1 1 0 0 1 1-1h3.5a1 1 0 0 1 1 1c0 1.25.2 2.45.57 3.57a1 1 0 0 1-.25 1z"/></svg>
            555.302.9817
          </li>
          <li>
            <svg viewBox="0 0 24 24" aria-hidden="true"><path d="M2 5h20v14H2z M2 5l10 8 10-8" fill="none" stroke="currentColor" stroke-width="2"/></svg>
            info@rkpadvisory.net
          </li>
          <li>
            <svg viewBox="0 0 24 24" aria-hidden="true"><g fill="none" stroke="currentColor" stroke-width="2"><circle cx="12" cy="12" r="10"/><path d="M2 12h20M12 2c3 3 3 17 0 20M12 2c-3 3-3 17 0 20"/></g></svg>
            www.rkpadvisory.net
          </li>
        </ul>
      </div>
    </section>

    <section class="card card-front" aria-label="Business card front">
      <p class="brand-name">RKP Advisory</p>
      <p class="brand-tagline">Virtual Assistance</p>
    </section>
  </main>
</body>
</html>
```